Holiday Club Flyer for 2026

Hi Ferncraft. We need a new flyer making for our holiday club for this year. You have made the last few which have always been good. This year the theme is space so please could you change the design to a space theme. The dates of the Holiday club are 28th, 29th and 30th October. It is the same venue, same timings and same activities that happen, we need the dates updating and the them of the flyer changing to space. I have attached last years flyer for you as a reminder.

```html
<!DOCTYPE html>
<html lang="en">
<head>
<meta charset="utf-8">
<title>Mission Discover Space – Holiday Club Flyer</title>
<link rel="stylesheet" href="https://fonts.googleapis.com/css2?family=Bebas+Neue&family=Playfair+Display:wght@900&family=Poppins:wght@400;500;600;700;800&display=swap">
<style>
:root{
  --paper:#ffffff;
  --space-deep:#0b0d1c;
  --space-mid:#1a1530;
  --teal:#33f0ea;
  --pill-a:#1f6a7c;
  --pill-b:#2461c9;
  --tab-navy:#1b2b5e;
  --line:#e8ecf3;
  --white:#ffffff;
  --yellow:#ffe81a;
  --green:#7ed321;
  --footer:#050a18;
  --email-band:#1c6f95;
}
*{margin:0;padding:0;box-sizing:border-box}
html,body{width:1200px;height:781px;overflow:hidden;background:var(--paper)}
body{position:relative;font-family:"Poppins",sans-serif;color:var(--white)}

.flyer{position:absolute;top:46px;width:532px;height:688px;overflow:hidden}
.flyer--info{left:44px}
.flyer--cover{left:606px}

.space-art{position:absolute;inset:0}
.flyer--info .space-art{
  background:
    radial-gradient(ellipse 55% 18% at 50% 34%, rgba(217,100,31,.45), transparent 70%),
    radial-gradient(ellipse 45% 30% at 85% 80%, rgba(138,42,37,.55), transparent 70%),
    radial-gradient(ellipse 40% 25% at 15% 80%, rgba(74,38,80,.55), transparent 70%),
    linear-gradient(180deg,var(--space-mid) 0%,var(--space-deep) 55%,var(--space-mid) 100%);
}
.flyer--cover .space-art{
  background:
    radial-gradient(ellipse 50% 22% at 50% 32%, rgba(217,100,31,.4), transparent 70%),
    radial-gradient(ellipse 55% 35% at 40% 70%, rgba(217,100,31,.75), transparent 70%),
    radial-gradient(ellipse 40% 30% at 85% 88%, rgba(200,40,50,.6), transparent 70%),
    radial-gradient(ellipse 30% 20% at 70% 55%, rgba(60,50,80,.7), transparent 70%),
    linear-gradient(180deg,var(--space-mid) 0%,var(--space-deep) 45%,#2a0f10 100%);
}

.mission-pill{
  position:absolute;left:50%;transform:translateX(-50%);
  background:linear-gradient(90deg,var(--pill-a),var(--pill-b));
  border-radius:999px;font-weight:800;letter-spacing:.02em;
  display:flex;align-items:center;justify-content:center;
}
.title-discover{
  position:absolute;left:0;right:0;text-align:center;white-space:nowrap;
  font-family:"Playfair Display",serif;font-weight:900;letter-spacing:.04em;line-height:1;
}
.title-space{
  position:absolute;left:0;right:0;text-align:center;white-space:nowrap;
  font-family:"Bebas Neue",sans-serif;color:var(--teal);line-height:1;
}

/* info side */
.flyer--info .mission-pill{top:70px;width:98px;height:24px;font-size:15px}
.flyer--info .title-discover{top:106px;font-size:36px}
.flyer--info .title-space{top:147px;font-size:52px;letter-spacing:.09em}
.tagline{position:absolute;top:205px;left:0;right:0;text-align:center;font-size:9.6px;font-weight:500;letter-spacing:.01em;white-space:nowrap}

.frame{position:absolute;border:1.5px solid var(--line);border-radius:12px}
.tab{
  position:absolute;left:50%;transform:translateX(-50%);
  background:var(--tab-navy);border:1.2px solid var(--line);border-radius:3px;
  font-size:9.5px;font-weight:600;display:flex;align-items:center;justify-content:center;
}
.dates{left:114px;top:248px;width:290px;height:68px;display:flex}
.dates .tab{top:-11px;width:72px;height:18px}
.date{flex:1;display:flex;flex-direction:column;align-items:center;justify-content:center;padding-top:6px}
.date + .date{border-left:1.5px solid var(--line);margin:10px 0 8px;padding-top:0}
.date__day{font-size:18.5px;font-weight:600;line-height:1.2}
.date__month{font-size:9.5px;font-weight:600}

.times{left:103px;top:347px;width:133px;height:127px}
.times .tab{top:-8px;width:72px;height:18px}
.time-block{text-align:center;white-space:nowrap}
.time-block--drop{margin-top:16px}
.time__value{font-size:19px;font-weight:600;line-height:1.2}
.time__note{font-size:8px;font-weight:600}
.times hr{border:0;border-top:1px solid var(--line);width:92px;margin:8px auto 6px}

.location{left:251px;top:347px;width:173px;height:127px;text-align:center}
.location .tab{top:-8px;width:72px;height:18px}
.venue{margin-top:22px;font-size:8px;font-weight:600;line-height:1.6}
.location hr{border:0;border-top:1px solid var(--line);width:114px;margin:4px auto 9px}
.activities{font-size:8.1px;font-weight:600;line-height:1.25;padding:0 8px}
.activities .highlight{color:var(--yellow)}

.register{position:absolute;left:106px;top:495px;width:322px;height:23px;border:1.2px solid var(--line);display:flex;font-weight:600;white-space:nowrap}
.register__label{width:84px;flex:none;font-size:10px;display:flex;align-items:center;justify-content:center}
.register__url{flex:1;min-width:0;background:var(--tab-navy);border-left:1.2px solid var(--line);font-size:10.2px;letter-spacing:-.01em;display:flex;align-items:center;justify-content:center;overflow:hidden}

.age-badge{
  position:absolute;left:130px;top:539px;width:84px;height:84px;border-radius:50%;
  border:3px solid #c9d3dc;background:var(--space-deep);
  display:flex;align-items:center;justify-content:center;text-align:center;
  font-size:7.6px;font-weight:600;line-height:1.65;
}

.club-name{position:absolute;display:flex;align-items:center;font-weight:800;color:var(--white);line-height:.95;white-space:nowrap}
.club-name__dot{border-radius:50%;background:var(--green);flex:none}
.flyer--info .club-name{left:246px;top:552px;gap:12px;font-size:20px}
.flyer--info .club-name__dot{width:44px;height:44px}

.footer{position:absolute;left:0;right:0;bottom:0;height:54px;background:var(--footer)}
.footer__address{position:absolute;left:79px;top:10px;font-size:11px;font-weight:600;line-height:1.5;white-space:nowrap}
.footer__email{position:absolute;right:0;bottom:0;width:179px;height:24px;background:var(--email-band);font-size:8px;font-weight:600;display:flex;align-items:center;justify-content:center;white-space:nowrap}

/* cover side */
.flyer--cover .mission-pill{top:47px;width:189px;height:44px;font-size:31px}
.flyer--cover .title-discover{top:121px;font-size:66px}
.flyer--cover .title-space{top:195px;font-size:96px;letter-spacing:.1em}
.flyer--cover .club-name{left:26px;top:316px;gap:12px;font-size:24px}
.flyer--cover .club-name__dot{width:52px;height:52px}
</style>
</head>
<body>

<section class="flyer flyer--info">
  <div class="space-art" role="img" aria-label="Deep space illustration with planets and glowing red-orange nebula clouds"></div>
  <div class="mission-pill">MISSION</div>
  <h1 class="title-discover">DISCOVER</h1>
  <div class="title-space">SPACE</div>
  <p class="tagline">GET READY FOR AN OUT-OF-THIS-WORLD ADVENTURE AT HOLIDAY CLUB!</p>

  <div class="frame dates">
    <div class="tab">DATES</div>
    <div class="date"><span class="date__day">28TH</span><span class="date__month">OCTOBER</span></div>
    <div class="date"><span class="date__day">29TH</span><span class="date__month">OCTOBER</span></div>
    <div class="date"><span class="date__day">30TH</span><span class="date__month">OCTOBER</span></div>
  </div>

  <div class="frame times">
    <div class="tab">TIME</div>
    <div class="time-block time-block--drop"><div class="time__value">8:45 AM</div><div class="time__note">DROP OFF FROM</div></div>
    <hr>
    <div class="time-block"><div class="time__value">12:30 PM</div><div class="time__note">COLLECT YOUR CHILDREN</div></div>
  </div>

  <div class="frame location">
    <div class="tab">LOCATION</div>
    <p class="venue">HOLLYBROOK CHAPEL<br>LARKFIELD ROAD</p>
    <hr>
    <p class="activities">Featuring games, bible stories, quizzes, craft&amp; more!<span class="highlight">Picnic lunch is included</span></p>
  </div>

  <div class="register">
    <span class="register__label">Register At</span>
    <span class="register__url">https://hollybrook.church/holiday-club</span>
  </div>

  <div class="age-badge">RECEPTION<br>TO<br>YEAR 7</div>

  <div class="club-name"><span class="club-name__dot"></span><span>Beacon<br>Holiday Club</span></div>

  <footer class="footer">
    <p class="footer__address">Hollybrook Chapel, Larkfield Road,<br>Ashford, AB1 2CD</p>
    <p class="footer__email">SAM@HOLLYBROOKCHAPEL.ORG</p>
  </footer>
</section>

<section class="flyer flyer--cover">
  <div class="space-art" role="img" aria-label="Space illustration of an astronaut riding a rocket through fiery orange nebula clouds among planets"></div>
  <div class="mission-pill">MISSION</div>
  <h2 class="title-discover">DISCOVER</h2>
  <div class="title-space">SPACE</div>
  <div class="club-name"><span class="club-name__dot"></span><span>Beacon<br>Holiday Club</span></div>
</section>

</body>
</html>
```